MRT Property - Business Cards

Looking for a business card & general letterhead, signage etc design for our new logo.

Colours:
000a20
0056a2
00b5ef
0088ce
68cef2

Fonts:
Poppins
Karla

Please keep look and feel of new brand - example in the zip package I sent.

```html
<!DOCTYPE html>
<html lang="en">
<head>
<meta charset="utf-8">
<title>MRT Property – Business Cards</title>
<link rel="stylesheet" href="https://fonts.googleapis.com/css2?family=Poppins:wght@400;600&display=swap">
<style>
  :root {
    --backdrop: #1b1c20;
    --navy-deep: #000a20;
    --navy-card: #121530;
    --brand-blue: #0056a2;
    --brand-mid: #0088ce;
    --brand-cyan: #00b5ef;
    --brand-light: #68cef2;
    --ink-light: #ffffff;
    --ink-soft: #d9dce8;
  }
  * { box-sizing: border-box; margin: 0; padding: 0; }
  html, body { width: 1200px; height: 900px; overflow: hidden; }
  body {
    background: var(--backdrop);
    font-family: "Poppins", sans-serif;
    position: relative;
  }
  .card {
    position: absolute;
    width: 560px;
    height: 320px;
    border-radius: 18px;
    overflow: hidden;
    background: var(--navy-card);
    border-bottom: 9px solid var(--brand-blue);
    box-shadow: 0 18px 40px rgba(0,0,0,0.45);
  }
  .card-back { left: 70px; top: 130px; }
  .card-front { left: 570px; top: 450px; }

  .pattern-field {
    position: absolute;
    inset: 0;
    background: linear-gradient(115deg, #3a4c9a 0%, #263376 22%, #161a3c 50%, #0e1128 100%);
  }
  .back-wordmark {
    position: absolute;
    right: 36px;
    bottom: 44px;
    font-size: 26px;
    font-weight: 600;
    color: var(--ink-light);
    letter-spacing: 0.5px;
  }

  .front-content {
    position: absolute;
    left: 38px;
    top: 34px;
    color: var(--ink-light);
  }
  .front-wordmark {
    font-size: 44px;
    font-weight: 600;
    line-height: 1.05;
    color: var(--ink-light);
  }
  .holder-name {
    margin-top: 22px;
    font-size: 22px;
    font-weight: 400;
    line-height: 1.1;
  }
  .holder-role {
    font-size: 13px;
    font-weight: 400;
    color: var(--ink-soft);
    letter-spacing: 0.3px;
  }
  .office-address {
    margin-top: 14px;
    font-size: 13px;
    line-height: 1.35;
    color: var(--ink-soft);
  }
  .contact-list {
    list-style: none;
    margin-top: 12px;
    font-size: 13px;
    color: var(--ink-soft);
  }
  .contact-list li {
    display: flex;
    align-items: center;
    gap: 10px;
    line-height: 1.7;
  }
  .contact-icon { width: 14px; height: 14px; flex: none; }
</style>
</head>
<body>

  <section class="card card-back" aria-label="Card back">
    <div class="pattern-field" role="img" aria-label="Repeating brand pattern fading from bright blue to deep navy"></div>
    <div class="back-wordmark">MRT Property</div>
  </section>

  <section class="card card-front" aria-label="Card front">
    <div class="front-content">
      <div class="front-wordmark">MRT Property</div>
      <p class="holder-name">Daniel Hart</p>
      <p class="holder-role">Managing Director</p>
      <p class="office-address">24 Cedar Ridge Road<br>Fairview, TN 37062</p>
      <ul class="contact-list">
        <li>
          <svg class="contact-icon" viewBox="0 0 24 24" aria-hidden="true"><path fill="#0088ce" d="M6.6 10.8a15.1 15.1 0 0 0 6.6 6.6l2.2-2.2c.3-.3.7-.4 1-.2 1.1.4 2.3.6 3.6.6.6 0 1 .4 1 1V20c0 .6-.4 1-1 1A17 17 0 0 1 3 4c0-.6.4-1 1-1h3.5c.6 0 1 .4 1 1 0 1.3.2 2.5.6 3.6.1.3 0 .7-.2 1z"/></svg>
          555.210.4478
        </li>
        <li>
          <svg class="contact-icon" viewBox="0 0 24 24" aria-hidden="true"><path fill="#0088ce" d="M3 5h18v14H3z"/><path fill="none" stroke="#121530" stroke-width="1.8" d="M3 5l9 7 9-7"/></svg>
          info@mrtproperty.com
        </li>
        <li>
          <svg class="contact-icon" viewBox="0 0 24 24" aria-hidden="true"><circle cx="12" cy="12" r="9" fill="none" stroke="#0088ce" stroke-width="2"/><path fill="none" stroke="#0088ce" stroke-width="1.6" d="M3 12h18M12 3c3 3 3 15 0 18M12 3c-3 3-3 15 0 18"/></svg>
          www.mrtproperty.com
        </li>
      </ul>
    </div>
  </section>

</body>
</html>
```